Push notification screens at app start up

We have an existing news publication app platform and are adding categories to push notifications.

We need two screens designed (each for Zorbel, Quillet and Android for a total of 6d) that show when the app is first launched.

The workflow of our app:
0. app launch screen while webservices run (no work needed)
1. information screen to the user promoting the benefits of push notification with "Next" button. (see concept attached)
2. Push categories selection screen. This will have list of category types, with on/off switch.

"Select the categories that you wish to receive occasional notices:
Breaking News (on/off switch)
Local News (on/off switch)
Sports (on/off switch)
Local Events (on/off switch)
Weather Alerts (on/off switch)
Local Deals (on/off switch)"

"Enable these categories on the next screen."
"Next" button

Background:
When I was looking around at app designs, I came across this one (http://www.plinthworks.example/design/7719034) and I really liked it. We obviously have different features on our screen, but I’d like to have this same feel. The colors used in this design are perfect.

UPDATE: I do not mean to limit your design to match the layout as the one mentioned above. Please use your creativity for the layout.

Our standard font in Helvetica Neue.

Notes:
- our app is developed for all phone devices from Zorbel 4 to Zorbel 6, so designs should be thoughtful of vertical scrolling if needed.
- our app is developed for Quillets, so we'll need designs completed as well. (We can finalize Zorbel design first, then translate the design to Quillet.)
- our app is developed for Android phones (not tablets), so we'll need designs completed as well. (We can finalize iOS design first, then translater to Android UI design guidelines).

We hope to establish a good on-going relationship with the designer for as-needed work in the future.

News

• Helvetica Neue

• Clean designs. No clutter.
• We would likely go with the standard on/off switches for both iOS and Android, but are open to small custom variations.

```html
<!DOCTYPE html>
<html lang="en">
<head>
<meta charset="utf-8">
<title>Push categories</title>
<link rel="stylesheet" href="https://fonts.googleapis.com/css2?family=Roboto:wght@300;400&display=swap">
<style>
  :root {
    --brand-blue: #4cbde8;
    --brand-blue-dark: #38afdd;
    --screen-bg: #efeff0;
    --text-muted: #6f7478;
    --divider: #dcdee0;
    --white: #ffffff;
    --switch-off-track: #f7f7f7;
    --switch-off-border: #c9cdd0;
    --switch-off-text: #a3a8ac;
  }
  * { box-sizing: border-box; margin: 0; padding: 0; }
  html, body {
    width: 1200px; height: 2352px; overflow: hidden;
    background: var(--screen-bg);
    font-family: "Roboto", "Helvetica Neue", Arial, sans-serif;
    font-weight: 300;
  }
  .screen { position: relative; width: 1200px; height: 2352px; background: var(--screen-bg); }

  .status-bar {
    height: 68px; background: var(--brand-blue); color: var(--white);
    display: flex; align-items: center; justify-content: space-between;
    padding: 0 28px; font-size: 30px; font-weight: 400;
  }
  .status-left, .status-right { display: flex; align-items: center; gap: 14px; width: 360px; }
  .status-right { justify-content: flex-end; }
  .signal { display: flex; gap: 6px; }
  .signal span { width: 14px; height: 14px; border-radius: 50%; background: var(--white); }
  .signal span.weak { background: transparent; border: 2px solid var(--white); }
  .battery { width: 62px; height: 28px; border: 2px solid var(--white); border-radius: 5px; padding: 3px; position: relative; }
  .battery::after { content: ""; position: absolute; right: -7px; top: 8px; width: 4px; height: 10px; background: var(--white); border-radius: 0 2px 2px 0; }
  .battery i { display: block; height: 100%; background: var(--white); border-radius: 2px; }

  .nav-bar {
    height: 132px; background: var(--brand-blue); color: var(--white);
    display: flex; align-items: center; justify-content: center; position: relative;
    font-size: 54px; font-weight: 300;
  }
  .nav-back { position: absolute; left: 44px; top: 44px; }

  .intro {
    padding: 70px 60px 40px; font-size: 46px; line-height: 1.4; color: var(--text-muted);
  }

  .category-list { list-style: none; margin: 0 40px; border-top: 2px solid var(--divider); }
  .category {
    height: 150px; display: flex; align-items: center;
    border-bottom: 2px solid var(--divider); padding: 0 20px;
  }
  .category-icon { width: 104px; height: 104px; flex: none; }
  .category-name { flex: 1; margin-left: 40px; font-size: 44px; color: var(--text-muted); }

  .switch {
    width: 180px; height: 76px; border-radius: 38px; position: relative;
    font-size: 30px; font-weight: 400; display: flex; align-items: center;
  }
  .switch-on { background: var(--brand-blue); color: var(--white); padding-left: 26px; }
  .switch-on::after {
    content: ""; position: absolute; right: 6px; top: 6px; width: 64px; height: 64px;
    border-radius: 50%; background: var(--white);
  }
  .switch-off {
    background: var(--switch-off-track); border: 2px solid var(--switch-off-border);
    color: var(--switch-off-text); justify-content: flex-end; padding-right: 24px;
  }
  .switch-off::before {
    content: ""; position: absolute; left: 4px; top: 4px; width: 64px; height: 64px;
    border-radius: 50%; background: var(--white); box-shadow: 0 2px 6px rgba(0,0,0,0.25);
  }

  .next-button {
    position: absolute; left: 0; bottom: 0; width: 1200px; height: 166px;
    background: var(--brand-blue); color: var(--white);
    display: flex; align-items: center; justify-content: center; gap: 24px;
    font-size: 54px; font-weight: 300; letter-spacing: 2px;
  }
</style>
</head>
<body>
<main class="screen">
  <header>
    <div class="status-bar">
      <div class="status-left">
        <div class="signal"><span></span><span></span><span></span><span class="weak"></span><span class="weak"></span></div>
        <span>KESTREL</span>
        <svg width="36" height="28" viewBox="0 0 36 28"><path d="M2 9a23 23 0 0 1 32 0M7 15a15 15 0 0 1 22 0M12 21a7 7 0 0 1 12 0" fill="none" stroke="#fff" stroke-width="3.5" stroke-linecap="round"/><circle cx="18" cy="25" r="3" fill="#fff"/></svg>
      </div>
      <span class="status-time">4:21 PM</span>
      <div class="status-right">
        <svg width="20" height="32" viewBox="0 0 20 32"><path d="M3 9l13 13-6 6V4l6 6L3 23" fill="none" stroke="#fff" stroke-width="2.5" stroke-linejoin="round"/></svg>
        <span>100%</span>
        <div class="battery"><i></i></div>
      </div>
    </div>
    <div class="nav-bar">
      <svg class="nav-back" width="28" height="46" viewBox="0 0 28 46"><path d="M24 4L6 23l18 19" fill="none" stroke="#fff" stroke-width="4" stroke-linecap="round" stroke-linejoin="round"/></svg>
      <h1 style="font-size:inherit;font-weight:inherit">Push categories</h1>
    </div>
  </header>

  <p class="intro">Select the categories that you wish to receive occasional notices:</p>

  <ul class="category-list">
    <li class="category">
      <svg class="category-icon" viewBox="0 0 104 104"><circle cx="52" cy="52" r="52" fill="var(--brand-blue)"/><path d="M30 46h10l22-12v36L40 58H30z" fill="#fff"/><path d="M38 58l5 14h8l-4-14" fill="#fff"/><path d="M70 42q6 10 0 20" stroke="#fff" stroke-width="4" fill="none" stroke-linecap="round"/></svg>
      <span class="category-name">Breaking News</span>
      <span class="switch switch-on">ON</span>
    </li>
    <li class="category">
      <svg class="category-icon" viewBox="0 0 104 104"><circle cx="52" cy="52" r="52" fill="var(--brand-blue)"/><rect x="28" y="30" width="48" height="44" rx="4" fill="none" stroke="#fff" stroke-width="4"/><path d="M28 42h48M38 26v8M66 26v8M36 52h8M48 52h8M60 52h8M36 62h8M48 62h8M60 62h8" stroke="#fff" stroke-width="4"/></svg>
      <span class="category-name">Local News</span>
      <span class="switch switch-on">ON</span>
    </li>
    <li class="category">
      <svg class="category-icon" viewBox="0 0 104 104"><circle cx="52" cy="52" r="52" fill="var(--brand-blue)"/><circle cx="52" cy="52" r="22" fill="none" stroke="#fff" stroke-width="4"/><path d="M30 52h44M52 30v44M36 36q10 16 0 32M68 36q-10 16 0 32" stroke="#fff" stroke-width="3" fill="none"/></svg>
      <span class="category-name">Sports</span>
      <span class="switch switch-on">ON</span>
    </li>
    <li class="category">
      <svg class="category-icon" viewBox="0 0 104 104"><circle cx="52" cy="52" r="52" fill="var(--brand-blue)"/><rect x="28" y="32" width="40" height="40" rx="4" fill="none" stroke="#fff" stroke-width="4"/><path d="M28 44h40M38 28v8M58 28v8" stroke="#fff" stroke-width="4"/><circle cx="70" cy="66" r="12" fill="#fff"/><path d="M64 66l4 4 8-8" stroke="var(--brand-blue)" stroke-width="3" fill="none"/></svg>
      <span class="category-name">Local Events</span>
      <span class="switch switch-off">OFF</span>
    </li>
    <li class="category">
      <svg class="category-icon" viewBox="0 0 104 104"><circle cx="52" cy="52" r="52" fill="var(--brand-blue)"/><circle cx="60" cy="40" r="10" fill="none" stroke="#fff" stroke-width="4"/><path d="M60 22v4M74 26l-3 3M78 40h-4" stroke="#fff" stroke-width="4" stroke-linecap="round"/><path d="M34 72h34a10 10 0 0 0 0-20 14 14 0 0 0-26 2 9 9 0 0 0-8 18z" fill="#fff"/></svg>
      <span class="category-name">Weather Alerts</span>
      <span class="switch switch-on">ON</span>
    </li>
    <li class="category">
      <svg class="category-icon" viewBox="0 0 104 104"><circle cx="52" cy="52" r="52" fill="var(--brand-blue)"/><path d="M30 30h22l24 24-22 22-24-24z" fill="none" stroke="#fff" stroke-width="4" stroke-linejoin="round"/><circle cx="41" cy="41" r="5" fill="#fff"/></svg>
      <span class="category-name">Local Deals</span>
      <span class="switch switch-off">OFF</span>
    </li>
  </ul>

  <div class="next-button">
    <span>NEXT</span>
    <svg width="22" height="38" viewBox="0 0 22 38"><path d="M3 3l16 16L3 35" fill="none" stroke="#fff" stroke-width="3.5" stroke-linecap="round" stroke-linejoin="round"/></svg>
  </div>
</main>
</body>
</html>
```